Detail Shop Business card design

i need a business card design for my new detailing company called 'Brisk's Polish Works'. i want an all black and white design . simple, direct and to the point. i want the designer to choose a fitting font to match the logothe front should have logo, address, phone and email and the back side should have a slogan and text indicating that we offer services on anything including cars, trucks, motorcycles and RVs. slogan will read "we take pride in your ride"
maybe also very small on the back side the IG icon with Brisks_Polish_Works

phone 208.417.6352
address 3847 E Larkin Ave
Spokane WA 99214
email: BrisksPolish@mailvexo.com

Target Market(s)

all ages , auto enthusiasts

Industry/Entity Type

Automotive

Contact Information for Business Card

the front should have logo, address, phone and email and the back side should have a slogan and text indicating that we offer services on anything including cars, trucks, motorcycles and RVs. slogan will read "we take pride in your ride"

phone 208.417.6352
address 3847 E Larkin Ave
Spokane WA 99214

Colors
000000
ffffff

Requirements
Must have
• bold font and very simple design with good spacing
Nice to have
• anything creative from the designer indicating we service any types of vehicles
Should not have
• any colors ,

```html
<!DOCTYPE html>
<html lang="en">
<head>
<meta charset="utf-8">
<title>Brisk's Polish Works – Business Card</title>
<link href="https://fonts.googleapis.com/css2?family=Open+Sans:wght@400;700;800&display=swap" rel="stylesheet">
<style>
  :root {
    --ink: #000000;
    --paper: #ffffff;
    --backdrop: #dcdcdc;
    --card-w: 520px;
    --card-h: 297px;
  }
  html, body {
    margin: 0;
    padding: 0;
    width: 1200px;
    height: 800px;
    overflow: hidden;
    background: var(--backdrop);
    font-family: "Open Sans", Arial, sans-serif;
  }
  .canvas {
    width: 1200px;
    height: 800px;
    display: flex;
    align-items: center;
    justify-content: center;
    gap: 40px;
  }
  .card {
    position: relative;
    width: var(--card-w);
    height: var(--card-h);
    box-sizing: border-box;
    box-shadow: 0 6px 18px rgba(0,0,0,0.18);
  }
  .card__frame {
    position: absolute;
    inset: 14px;
    border: 2px solid;
  }
  .card--contact {
    background: var(--ink);
    color: var(--paper);
  }
  .card--contact .card__frame { border-color: var(--paper); }
  .card--services {
    background: var(--paper);
    color: var(--ink);
  }
  .card--services .card__frame { border-color: var(--ink); }

  .contact {
    position: absolute;
    top: 84px;
    left: 0;
    right: 0;
    text-align: center;
    font-size: 14px;
    line-height: 1.45;
  }
  .contact__name { font-weight: 700; font-size: 16px; }
  .slogan {
    position: absolute;
    left: 0;
    right: 0;
    bottom: 46px;
    text-align: center;
    font-size: 15px;
    letter-spacing: 0.55em;
    padding-left: 0.55em;
  }

  .services {
    position: absolute;
    top: 60px;
    left: 0;
    right: 0;
    display: flex;
    flex-direction: column;
    align-items: center;
  }
  .brand {
    display: flex;
    align-items: center;
    gap: 10px;
    font-weight: 800;
    font-size: 22px;
    margin-bottom: 22px;
  }
  .brand__dot {
    width: 14px;
    height: 14px;
    border-radius: 50%;
    background: var(--ink);
  }
  .services__title { font-weight: 700; font-size: 16px; }
  .services__list { font-size: 13px; margin-top: 2px; }
</style>
</head>
<body>
<main class="canvas">
  <section class="card card--contact">
    <div class="card__frame"></div>
    <div class="contact">
      <div><span class="contact__name">Dale Marsh</span> | Owner</div>
      <div>P: 208.417.6352 | E: BrisksPolish@mailvexo.com</div>
      <div>3847 E Larkin Ave, Spokane WA 99214</div>
    </div>
    <div class="slogan">we take pride in your ride</div>
  </section>

  <section class="card card--services">
    <div class="card__frame"></div>
    <div class="services">
      <div class="brand"><span class="brand__dot"></span>Brisk's Polish Works</div>
      <div class="services__title">we offer services</div>
      <div class="services__list">cars | trucks | motorcycle | boats and rvs</div>
    </div>
  </section>
</main>
</body>
</html>
```